Explosive, chemical reaction of creativity!

Web design for a digital marketing company. The unconventional is encouraged!
This is for a cool, young, geographically diverse company (sketchhive... you are all part of our team!!!)... we build websites but our real specialty is "search experience optimization".... creating conversion focused content, SEO (including content), and social media.

Target Market(s)

small to medium size businesses, law firms, medical practices, municipalities

Industry/Entity Type

Marketing

Number of Pages Required

2 page

Requirements
Must have
• WOW
• something different and special... we've been playing with a science theme (www.fernquillmedia.marketing) but we are open to different looks, layouts, etc.
• we nee a homepage design and an interior page design
• content needs to include: Marketing Catalysts (about us), Our Formula (services), Chemical Reactions(Results/Our Clients),
• FREE Online Prism Check
• Let us put together an objective snapshot of your digital presence for you.
Nice to have
• we are open to the use of background video (chemical reaction???)
• we are open to cool and different imagery
Should not have
• template look like most other websites

```html
<!DOCTYPE html>
<html lang="en">
<head>
<meta charset="utf-8">
<title>Fernquill Media Marketing</title>
<link href="https://fonts.googleapis.com/css2?family=Lato:wght@300;400;700;900&family=Raleway:wght@300;400;500&display=swap" rel="stylesheet">
<style>
:root{
  --page:#ebebeb;
  --ink:#1d1d1d;
  --ink-soft:#444;
  --white:#ffffff;
  --accent:#29aee6;
  --slate:#2c3135;
  --band:#5e6569;
  --news:#f1f1f1;
  --charcoal:#474747;
  --map:#2b2b2b;
  --box:#1b1b1b;
  --brand:#1f3b63;
}
*{margin:0;padding:0;box-sizing:border-box}
html,body{width:1200px;height:3854px;overflow:hidden}
body{position:relative;background:var(--page);font-family:'Lato',Arial,sans-serif;color:var(--ink)}
.abs{position:absolute}
.center{left:0;width:1200px;text-align:center}

/* header */
.site-header{top:0;left:0;width:1200px;height:106px;background:rgba(235,235,235,.94);z-index:5}
.brand{left:80px;top:26px;display:flex;align-items:center;gap:14px}
.brand-mark{width:48px;height:48px;background:var(--brand)}
.brand-name{font-weight:900;font-size:26px;color:var(--brand);letter-spacing:1px;line-height:1}
.social{display:flex;gap:8px}
.social span{width:24px;height:24px;border:1.5px solid #333;border-radius:50%;display:block}
.header-social{right:82px;top:18px}
.main-nav{right:80px;top:62px;display:flex;gap:28px;font-size:14px;font-weight:700}
.main-nav a{color:var(--ink);text-decoration:none;position:relative}
.main-nav a.active:after{content:"";position:absolute;left:0;right:0;bottom:-8px;height:2px;background:var(--ink)}

/* hero */
.hero-photo{top:0;left:0;width:1200px;height:617px;
  clip-path:polygon(0 0,100% 0,100% 475px,604px 617px,0 475px);
  background:
    radial-gradient(circle at 14% 58%,rgba(168,205,228,.75) 0,rgba(168,205,228,0) 22%),
    radial-gradient(circle at 88% 22%,rgba(190,220,238,.7) 0,rgba(190,220,238,0) 20%),
    radial-gradient(circle at 72% 80%,rgba(140,185,212,.55) 0,rgba(140,185,212,0) 24%),
    radial-gradient(circle at 40% 30%,rgba(110,150,178,.45) 0,rgba(110,150,178,0) 26%),
    linear-gradient(160deg,#2a4659 0%,#1c2f3d 50%,#243b4b 100%)}
.hero-title{top:196px;font-family:'Raleway',sans-serif;font-weight:300;font-size:52px;line-height:62px;color:var(--white)}
.hero-sub{top:334px;font-size:16px;line-height:26px;color:var(--white)}
.btn-outline{display:inline-block;border:2px solid var(--white);color:var(--white);font-weight:700;letter-spacing:1px;text-decoration:none}
.hero-btn{left:493px;top:414px;width:214px;height:62px;line-height:58px;font-size:24px;text-align:center}

/* intro */
.intro-title{left:80px;top:636px;font-family:'Raleway',sans-serif;font-size:38px;font-weight:400}
.intro-lead{left:80px;top:703px;width:440px;font-size:14px;font-weight:700;line-height:19px}
.intro-body{left:80px;top:752px;width:440px;font-size:12.5px;font-weight:700;line-height:19px}
.philosophy{left:663px;top:684px;width:427px;height:138px;background:var(--box);color:var(--white);padding:14px 18px}
.philosophy h3{font-family:'Raleway',sans-serif;font-weight:400;font-size:28px;margin-bottom:8px}
.philosophy .lead{font-size:13.5px;font-weight:700;margin-bottom:8px}
.philosophy p{font-size:12px;line-height:18px}
.touch-tab{right:-2px;top:660px;width:72px;height:168px;background:var(--accent);border-radius:84px 0 0 84px}
.touch-tab span{position:absolute;left:44px;top:30px;writing-mode:vertical-rl;color:var(--white);font-size:14px}

/* services */
.services-bg{top:879px;left:0;width:1200px;height:760px;
  background:
    radial-gradient(circle at 88% 32%,rgba(120,132,140,.55) 0,rgba(120,132,140,0) 16%),
    radial-gradient(circle at 64% 62%,rgba(110,122,130,.5) 0,rgba(110,122,130,0) 14%),
    radial-gradient(circle at 80% 8%,rgba(100,112,120,.45) 0,rgba(100,112,120,0) 12%),
    radial-gradient(ellipse at 80% 40%,#454d52 0%,var(--slate) 55%,#1f2326 100%)}
.rule{width:2px;height:58px;background:rgba(255,255,255,.75);left:599px}
.rule.dark{background:#555}
.spaced{font-family:'Raleway',sans-serif;font-weight:400;letter-spacing:14px;color:var(--white);font-size:34px}
.service{top:1062px;width:240px;text-align:center;color:var(--white)}
.service h4{font-size:18px;font-weight:700;letter-spacing:2px;display:flex;justify-content:center;align-items:center;gap:10px;padding-bottom:10px;border-bottom:1px solid rgba(255,255,255,.6)}
.service p{margin:14px auto 0;width:210px;font-size:12.5px;font-weight:700;line-height:19px}

.mission-band{top:0;left:0;width:1200px;height:3854px;pointer-events:none}
.body-copy{font-size:12.5px;font-weight:700;line-height:20px;color:var(--white)}

/* team */
.team-photo{top:1580px;left:0;width:1200px;height:760px;
  background:
    radial-gradient(ellipse at 18% 30%,rgba(214,190,160,.85) 0,rgba(214,190,160,0) 30%),
    radial-gradient(ellipse at 14% 78%,rgba(40,44,52,.8) 0,rgba(40,44,52,0) 28%),
    linear-gradient(90deg,#9c8b78 0%,#5f5b58 35%,#3f4650 70%,#2c3138 100%)}
.team-btn{left:383px;top:1990px;width:434px;height:53px;line-height:49px;text-align:center;font-size:15px;letter-spacing:7px}

/* news */
.news-title{color:var(--ink)}
.news-card{top:2344px;width:520px;display:flex;gap:18px}
.news-thumb{width:195px;height:117px;flex:none}
.news-card h5{font-size:15px;font-weight:900;margin-bottom:10px}
.news-card p{font-size:12.5px;line-height:17px;color:var(--ink-soft)}
.news-card a{display:block;margin-top:6px;font-size:11.5px;font-weight:700;color:var(--ink);text-decoration:underline}
.arrow-btn{top:2486px;width:36px;height:40px;border:1px solid #555;display:flex;align-items:center;justify-content:center}
.arrow-btn.dark{background:#222}

/* newsletter + check */
.map-bg{top:2990px;left:0;width:1200px;height:864px;background:linear-gradient(180deg,#2f2f2f,var(--map))}
.field{background:var(--white);height:37px;font-size:12px;color:#777;display:flex;align-items:center;justify-content:center}
.btn-solid{background:var(--accent);color:var(--white);font-size:14px;letter-spacing:2px;display:flex;align-items:center;justify-content:center}
.form-field{border:1px solid rgba(255,255,255,.55);color:var(--white);font-size:12px;padding:0 12px;display:flex;align-items:center}
.contact-item{top:3660px;display:flex;align-items:center;gap:16px;color:var(--white)}
.contact-item .ico{width:52px;height:52px;border:2px solid rgba(255,255,255,.5);border-radius:50%;display:flex;align-items:center;justify-content:center}
.contact-item b{font-size:13px;display:block}
.contact-item small{font-size:12px;display:block;line-height:15px}
.phone-num{font-size:24px;font-weight:700}
.footer-line{top:3752px;left:0;width:1200px;height:1px;background:rgba(255,255,255,.3)}
.copyright{left:80px;top:3781px;font-size:11px;color:#ccc}
.footer-social{right:82px;top:3774px}
.footer-social span{border-color:#aaa}
</style>
</head>
<body>

<div class="abs hero-photo" role="img" aria-label="Close-up photograph of a glass molecular model"></div>

<header class="abs site-header">
  <div class="abs brand"><span class="brand-mark"></span><span class="brand-name">FERNQUILL MEDIA</span></div>
  <div class="abs social header-social"><span></span><span></span><span></span></div>
  <nav class="abs main-nav">
    <a class="active" href="#">Home</a><a href="#">Marketing Catalysts</a><a href="#">Our Formula</a><a href="#">Chemical Reactions</a><a href="#">Contact Us</a>
  </nav>
</header>

<h1 class="abs center hero-title">It’s not rocket science,<br>it’s Fernquill Media science!</h1>
<p class="abs center hero-sub">Sales is the chemical reaction that results from “our formula” which is the right<br>combination of our digital marketing services.</p>
<a class="abs btn-outline hero-btn" href="#">GET STARTED</a>

<h2 class="abs intro-title">Using data for success</h2>
<p class="abs intro-lead">Search Engine Optimization has been replaced with Search Experience Optimization.</p>
<p class="abs intro-body">Lorem ipsum dolor sit amet, consectetuer adipiscing elit, seddiam nonummy nibh euismod . Lorem ipsum dolor sit amet, consectetuer adipiscing elit, seddiam nonummy .</p>
<div class="abs philosophy">
  <h3>Our Business Philosophy</h3>
  <p class="lead">Lorem ipsum dolor sit amet consectetur</p>
  <p>Lorem ipsum dolor sit amet, consectetuer adipiscing elit, seddiam nonummy nibh euismod .</p>
</div>
<div class="abs touch-tab"><span>Get in Touch</span>
  <svg class="abs" style="left:10px;top:64px" width="22" height="40" viewBox="0 0 22 40"><path d="M3 2 L19 20 L3 38" fill="none" stroke="#fff" stroke-width="2"/></svg>
</div>

<div class="abs services-bg" role="img" aria-label="Dark backdrop of glossy molecule spheres and bonds"></div>
<div class="abs team-photo" role="img" aria-label="Photograph of a smiling businesswoman with colleagues in an office"></div>

<svg class="abs mission-band" width="1200" height="3854" viewBox="0 0 1200 3854" aria-hidden="true">
  <polygon points="0,1190 1200,1400 1200,1700 0,1600" fill="#5e6569" opacity=".92"/>
  <polygon points="0,1600 1200,1700 1200,1760 0,1660" fill="#5e6569" opacity=".45"/>
  <polygon points="0,2300 1200,1953 1200,2600 0,2600" fill="#f1f1f1"/>
  <polygon points="0,2480 1200,2590 1200,2990 0,2990" fill="#474747"/>
</svg>

<div class="abs map-bg" role="img" aria-label="Faint dark street map backdrop"></div>
<svg class="abs" style="left:0;top:2989px" width="1200" height="170" viewBox="0 0 1200 170" aria-hidden="true">
  <polygon points="0,0 1200,0 604,160" fill="#474747"/>
</svg>

<div class="abs rule" style="top:905px"></div>
<h2 class="abs center spaced" style="top:986px">SERVICES</h2>
<div class="abs service" style="left:137px">
  <h4><svg width="26" height="18" viewBox="0 0 26 18"><path d="M6 17h15a5 5 0 0 0 0-10 7 7 0 0 0-13-1 5.5 5.5 0 0 0-2 11z" fill="#fff"/></svg>Website</h4>
  <p>You’ve got 10 seconds to grab the attention of a site viewer. We build for appearance, content, and functionality.</p>
</div>
<div class="abs service" style="left:479px">
  <h4><svg width="26" height="20" viewBox="0 0 26 20"><rect x="1" y="1" width="24" height="18" fill="#fff"/><circle cx="13" cy="10" r="5" fill="#2c3135"/><circle cx="13" cy="10" r="2.5" fill="#fff"/></svg>Content</h4>
  <p>Content is the most powerful element of our formula... It creates need, provokes emotion and sparks action.</p>
</div>
<div class="abs service" style="left:823px">
  <h4><svg width="20" height="20" viewBox="0 0 20 20"><circle cx="15" cy="4" r="3" fill="#fff"/><circle cx="5" cy="10" r="3" fill="#fff"/><circle cx="15" cy="16" r="3" fill="#fff"/><path d="M15 4L5 10L15 16" stroke="#fff" stroke-width="1.8" fill="none"/></svg>Social</h4>
  <p>We are obsessed with the latest trends and are always testing new ways to cultivate both following and engagement.</p>
</div>

<div class="abs rule" style="top:1440px"></div>
<h2 class="abs center spaced" style="top:1522px">MISSION</h2>
<p class="abs body-copy" style="left:295px;top:1573px;width:610px;text-align:center">Lorem ipsum dolor sit amet, consectetuer adipiscing elit, seddiam nonummy nibh euismod . Lorem ipsum dolor sit amet Lorem ipsum dolor sit. Lorem ipsum dolor sit amet, consectetuer adipiscing elit, seddiam nonummy nibh euismod . Lorem ipsum dolor sit amet Lorem ipsum dolor sit .</p>

<div class="abs rule" style="top:1778px"></div>
<h2 class="abs center spaced" style="top:1860px">MEET THE TEAM</h2>
<p class="abs body-copy" style="left:295px;top:1924px;width:610px;text-align:center">Lorem ipsum dolor sit amet, consectetuer adipiscing elit, seddiam nonummy nibh euismod . Lorem ipsum dolor sit amet Lorem ipsum dolor sit amet, Lorem ipsum dolor sit amet, consectetuer .</p>
<a class="abs btn-outline team-btn" href="#">READ MORE</a>

<div class="abs rule dark" style="top:2184px"></div>
<h2 class="abs center spaced news-title" style="top:2246px">LATEST NEWS</h2>
<article class="abs news-card" style="left:80px">
  <div class="news-thumb" role="img" aria-label="Photograph of hands using a tablet over paperwork" style="background:linear-gradient(135deg,#d9c3a8,#6f8fb0)"></div>
  <div><h5>Lorem ipsum dolor sit amet, consectet</h5><p>Lorem ipsum dolor sit amet, consectetuer adipiscing elit. Sed vitae magna tellus. Aenean ante nunc, semper nec cursus</p><a href="#">Read More »</a></div>
</article>
<article class="abs news-card" style="left:617px">
  <div class="news-thumb" role="img" aria-label="Photograph of a laptop on a desk" style="background:linear-gradient(135deg,#5a5a5a,#b7b7b7)"></div>
  <div><h5>Lorem ipsum dolor sit amet, consectet</h5><p>Lorem ipsum dolor sit amet, consectetuer adipiscing elit. Sed vitae magna tellus. Aenean ante nunc, semper nec cursus</p><a href="#">Read More »</a></div>
</article>
<div class="abs arrow-btn" style="left:1043px"><svg width="10" height="16" viewBox="0 0 10 16"><path d="M8 1L2 8L8 15" stroke="#333" stroke-width="2" fill="none"/></svg></div>
<div class="abs arrow-btn dark" style="left:1084px"><svg width="10" height="16" viewBox="0 0 10 16"><path d="M2 1L8 8L2 15" stroke="#fff" stroke-width="2" fill="none"/></svg></div>

<div class="abs rule" style="top:2716px"></div>
<h2 class="abs center spaced" style="top:2806px">NEWSLETTER SIGNUP</h2>
<div class="abs field" style="left:378px;top:2870px;width:444px">Enter Your Email Here</div>
<div class="abs btn-solid" style="left:524px;top:2937px;width:152px;height:39px">SUBSCRIBE</div>

<div class="abs rule" style="top:3190px"></div>
<h2 class="abs center spaced" style="top:3282px">FREE ONLINE PRISM CHECK</h2>
<div class="abs form-field" style="left:321px;top:3369px;width:265px;height:36px">Name</div>
<div class="abs form-field" style="left:609px;top:3369px;width:265px;height:36px">Email</div>
<div class="abs form-field" style="left:321px;top:3423px;width:265px;height:35px">Phone</div>
<div class="abs form-field" style="left:609px;top:3423px;width:265px;height:35px;justify-content:space-between">Subject<svg width="10" height="6" viewBox="0 0 10 6"><path d="M0 0h10L5 6z" fill="#fff"/></svg></div>
<div class="abs form-field" style="left:321px;top:3475px;width:553px;height:59px;align-items:flex-start;padding-top:8px">Message</div>
<div class="abs btn-solid" style="left:524px;top:3562px;width:152px;height:38px">SUBMIT</div>

<div class="abs contact-item" style="left:283px">
  <div class="ico"><svg width="18" height="24" viewBox="0 0 18 24"><path d="M9 1a8 8 0 0 0-8 8c0 6 8 14 8 14s8-8 8-14a8 8 0 0 0-8-8z" fill="#aaa"/><circle cx="9" cy="9" r="3" fill="#2b2b2b"/></svg></div>
  <div><b>FERNQUILL MEDIA MARKETING</b><small>2870 Harbor Loop Suite 210</small><small>Brightvale, TX 70412</small></div>
</div>
<div class="abs contact-item" style="left:648px">
  <div class="ico"><svg width="22" height="22" viewBox="0 0 24 24"><path d="M6 2l4 5-2 3c1 3 3 5 6 6l3-2 5 4-2 4C12 22 2 12 2 4z" fill="#aaa"/></svg></div>
  <div><small>CALL US TODAY</small><span class="phone-num">555-014-2290</span></div>
</div>

<div class="abs footer-line"></div>
<p class="abs copyright">Copyright © 2016 FERNQUILL MEDIA MARKETING . All Right Reserved</p>
<div class="abs social footer-social"><span></span><span></span><span></span></div>

</body>
</html>
```